Harborline Auto LLC

Car Dealer Customer Service
Address: 2874 Cresthaven Road, Shelbyville, TN 37162
web: www.harborlineautoxq.net
email: harborlineautoxq@mailnest.example
Phone: (931) 555-0148
Phone: (629) 555-0173

```html
<!DOCTYPE html>
<html lang="en">
<head>
<meta charset="utf-8">
<title>Harborline Auto – Business Card</title>
<link rel="stylesheet" href="https://fonts.googleapis.com/css2?family=Montserrat:ital,wght@0,400;0,500;0,800;1,400&display=swap">
<style>
  :root {
    --blue: #1f93cf;
    --blue-deep: #0f6ca6;
    --blue-logo: #1677b5;
    --gold: #e9ab33;
    --paper: #f7f7f5;
    --backdrop: #1c1c1e;
    --white: #ffffff;
  }
  * { box-sizing: border-box; margin: 0; padding: 0; }
  html, body { width: 1200px; height: 963px; overflow: hidden; }
  body {
    background: var(--backdrop);
    font-family: "Montserrat", sans-serif;
    display: flex;
    flex-direction: column;
    align-items: center;
    justify-content: center;
    gap: 44px;
  }
  .card {
    position: relative;
    width: 700px;
    height: 400px;
    overflow: hidden;
    box-shadow: 0 10px 30px rgba(0,0,0,.5);
  }
  .card-art { position: absolute; inset: 0; }

  /* front */
  .contact {
    position: absolute;
    left: 40px;
    top: 52px;
    color: var(--white);
    white-space: nowrap;
  }
  .contact-name { font-weight: 800; font-size: 21px; letter-spacing: .5px; text-transform: uppercase; }
  .contact-role { font-style: italic; font-size: 13px; margin-top: 2px; }
  .contact-address { font-size: 13px; line-height: 1.45; margin-top: 22px; }
  .contact-list { list-style: none; margin-top: 22px; font-size: 13px; line-height: 1.7; }
  .contact-list li { display: flex; align-items: center; gap: 8px; }
  .contact-icon {
    width: 14px; height: 14px; border-radius: 50%;
    background: var(--white); flex: none;
    display: flex; align-items: center; justify-content: center;
  }
  .contact-icon svg { width: 9px; height: 9px; }
  .front-brand {
    position: absolute;
    left: 392px;
    top: 182px;
    display: flex;
    align-items: center;
    gap: 10px;
    white-space: nowrap;
    color: var(--blue-logo);
    font-weight: 800;
    font-size: 25px;
    letter-spacing: 1px;
  }
  .brand-dot { width: 14px; height: 14px; border-radius: 50%; background: var(--gold); flex: none; }

  /* back */
  .card-back { background: linear-gradient(135deg, #1686c4 0%, #2a9fd8 50%, #1a7fc0 100%); }
  .back-brand {
    position: absolute;
    inset: 0;
    display: flex;
    align-items: center;
    justify-content: center;
    gap: 12px;
    color: var(--white);
    font-weight: 800;
    font-size: 40px;
    letter-spacing: 1.5px;
  }
  .back-brand .brand-dot { width: 18px; height: 18px; }
</style>
</head>
<body>

<section class="card card-front" aria-label="Business card front">
  <svg class="card-art" viewBox="0 0 700 400" width="700" height="400" aria-hidden="true">
    <defs>
      <linearGradient id="frontBlue" x1="0" y1="0" x2="1" y2="1">
        <stop offset="0" stop-color="#1a87c6"/>
        <stop offset="1" stop-color="#1f97d3"/>
      </linearGradient>
    </defs>
    <rect width="700" height="400" fill="url(#frontBlue)"/>
    <path d="M570 0 C430 50 350 200 370 400 L700 400 L700 0 Z" fill="var(--paper)"/>
    <path d="M550 0 C410 50 330 200 350 400" fill="none" stroke="var(--white)" stroke-width="6"/>
    <path d="M556 0 C416 50 337 200 357 400" fill="none" stroke="var(--blue-deep)" stroke-width="5"/>
    <path d="M566 0 C426 50 346 200 366 400" fill="none" stroke="var(--gold)" stroke-width="4"/>
  </svg>

  <div class="contact">
    <p class="contact-name">Marcus Delaney</p>
    <p class="contact-role">Manager</p>
    <p class="contact-address">2874 Cresthaven Road<br>Shelbyville, TN 37162</p>
    <ul class="contact-list">
      <li><span class="contact-icon"><svg viewBox="0 0 10 10"><path d="M2 1 L4 1 L4.6 3 L3.6 3.8 Q4.5 5.6 6.2 6.4 L7 5.4 L9 6 L9 8 Q5 9 1 3 Z" fill="var(--blue-deep)"/></svg></span>(931) 555-0148</li>
      <li><span class="contact-icon"><svg viewBox="0 0 10 10"><path d="M2 1 L4 1 L4.6 3 L3.6 3.8 Q4.5 5.6 6.2 6.4 L7 5.4 L9 6 L9 8 Q5 9 1 3 Z" fill="var(--blue-deep)"/></svg></span>(629) 555-0173</li>
      <li><span class="contact-icon"><svg viewBox="0 0 10 10"><rect x="1" y="2.5" width="8" height="5" fill="none" stroke="var(--blue-deep)" stroke-width="1"/><path d="M1 2.5 L5 5.5 L9 2.5" fill="none" stroke="var(--blue-deep)" stroke-width="1"/></svg></span>harborlineautoxq@mailnest.example</li>
      <li><span class="contact-icon"><svg viewBox="0 0 10 10"><circle cx="5" cy="5" r="3.8" fill="none" stroke="var(--blue-deep)" stroke-width="1"/><path d="M1.2 5 H8.8 M5 1.2 Q2.8 5 5 8.8 Q7.2 5 5 1.2" fill="none" stroke="var(--blue-deep)" stroke-width=".8"/></svg></span>www.harborlineautoxq.net</li>
    </ul>
  </div>

  <div class="front-brand"><span class="brand-dot"></span>HARBORLINE AUTO</div>
</section>

<section class="card card-back" aria-label="Business card back">
  <div class="back-brand"><span class="brand-dot"></span>HARBORLINE AUTO</div>
</section>

</body>
</html>
```